Business Card design for law firm = Brightvale Australia

We are seeking a new design for our business cards.
We are keeping our logo, which is attached.
We need space for
Name
Title
Address is , which is
Level 7
214 Marlowe Street
Sydney NSW 2047
Phone :
Mobile :
Fax :
Email :
DX :
website www.brightvale-example.com.au

Industry/Entity Type

Law Firm / Banking and Finance

Contact Information for Business Card

We are seeking a new design for our business cards. We are keeping our logo. We need space for Name Title Address is Level 7 214 Marlowe Street Sydney NSW 2047 Phone Mobile Fax Email DX website www.brightvale-example.com.au

Colors
0054AA
0677BA
7BADD7
CADEEF
E8F1F8

Requirements
Must have
• see our website for general feel www.brightvale-example.com.au

```html
<!DOCTYPE html>
<html lang="en">
<head>
<meta charset="utf-8">
<title>Brightvale Australia — Business Card</title>
<link rel="stylesheet" href="https://fonts.googleapis.com/css2?family=Cormorant+SC:wght@600&family=Roboto:wght@400&display=swap">
<style>
  :root {
    --stage: #e4e5e7;
    --brand-blue: #0a8ac4;
    --deep-blue: #1f55b0;
    --ink: #1e1e1e;
    --paper: #ffffff;
  }
  * { box-sizing: border-box; margin: 0; padding: 0; }
  html, body { width: 1200px; height: 900px; overflow: hidden; }
  body {
    background: var(--stage);
    display: flex;
    flex-direction: column;
    align-items: center;
    justify-content: center;
    gap: 56px;
    font-family: "Roboto", Arial, sans-serif;
  }
  .card {
    position: relative;
    width: 620px;
    height: 354px;
    border-radius: 24px;
    overflow: hidden;
    box-shadow: 0 6px 18px rgba(0,0,0,0.18);
  }

  /* Company name */
  .company-name {
    font-family: "Roboto", Arial, sans-serif;
    font-weight: 400;
    line-height: 1;
    white-space: nowrap;
  }

  /* Back side */
  .card--back { background: var(--brand-blue); }
  .card--back .company-name {
    position: absolute;
    left: 50%; top: 50%;
    transform: translate(-50%, -50%);
    color: var(--paper);
    font-size: 52px;
  }

  /* Front side */
  .card--front { background: var(--paper); }
  .card--front .company-name {
    position: absolute;
    left: 40px; top: 156px;
    color: var(--deep-blue);
    font-size: 42px;
  }

  .person {
    position: absolute;
    right: 46px; top: 30px;
    text-align: right;
  }
  .person__name {
    font-family: "Cormorant SC", Georgia, serif;
    font-weight: 600;
    font-size: 26px;
    color: var(--deep-blue);
    line-height: 1;
  }
  .person__title { font-size: 12.5px; color: var(--ink); margin-top: 4px; }
  .edge-tab {
    position: absolute;
    right: 0; top: 30px;
    width: 22px; height: 26px;
    background: var(--brand-blue);
  }

  .address {
    position: absolute;
    left: 68px; top: 228px;
    font-size: 12.5px;
    font-style: normal;
    line-height: 15px;
    color: var(--ink);
  }
  .contact-list {
    list-style: none;
    position: absolute;
    left: 68px; top: 264px;
    font-size: 12.5px;
    color: var(--ink);
  }
  .contact-list li { display: flex; align-items: center; gap: 6px; height: 15px; }
  .contact-list svg { width: 10px; height: 10px; fill: var(--deep-blue); flex: none; }
</style>
</head>
<body>

  <section class="card card--back" aria-label="Card back">
    <span class="company-name">Brightvale</span>
  </section>

  <section class="card card--front" aria-label="Card front">
    <span class="edge-tab"></span>
    <div class="person">
      <div class="person__name">Helena Marsh</div>
      <div class="person__title">Chief Legal Officer, BA, LLB (Hons)</div>
    </div>

    <span class="company-name">Brightvale</span>

    <address class="address">
      Level 7, 214 Marlowe Street<br>
      Sydney NSW 2047
    </address>

    <ul class="contact-list">
      <li>
        <svg viewBox="0 0 10 10" aria-label="Phone"><path d="M2 0.5 L3.6 2.6 L2.8 3.6 Q4 6 6.4 7.2 L7.4 6.4 L9.5 8 L8.4 9.5 Q3.5 9 0.5 1.6 Z"/></svg>
        02 5550 0142
      </li>
      <li>
        <svg viewBox="0 0 10 10" aria-label="Mobile"><path d="M2.5 0 H7.5 V10 H2.5 Z M3.4 1 V7.8 H6.6 V1 Z M4.5 8.4 H5.5 V9.3 H4.5 Z"/></svg>
        02 5550 0178
      </li>
      <li>
        <svg viewBox="0 0 10 10" aria-label="Fax"><path d="M2.5 0 H7.5 V3 H2.5 Z M0.5 3.5 H9.5 V7.5 H8 V6 H2 V7.5 H0.5 Z M2.8 6.6 H7.2 V10 H2.8 Z"/></svg>
        02 5550 0191
      </li>
      <li>
        <svg viewBox="0 0 10 10" aria-label="Email"><path d="M0 2 H10 V8.5 H0 Z M0.8 2.6 L5 5.8 L9.2 2.6 Z" fill-rule="evenodd"/></svg>
        helena.marsh@brightvale-example.com.au
      </li>
      <li>
        <svg viewBox="0 0 10 10" aria-label="Website"><circle cx="5" cy="5" r="4.6"/><path d="M0.5 5 H9.5 M5 0.4 Q2 5 5 9.6 M5 0.4 Q8 5 5 9.6" stroke="#fff" stroke-width="0.7" fill="none"/></svg>
        www.brightvale-example.com.au
      </li>
    </ul>
  </section>

</body>
</html>
```